Lark Vista Perks Needs a Website Design

We need a website design for a new service we are starting. Users enter a coupon in a redemption page and either create an account or sign in. they can then use the credits they accumulate from the coupons to purchase items listed on the site.

we need a design for the following:
-the coupon redemption page (with a choice to either sign in or create an account)
-a product listing page (with search filters and a search bar. the search bar can be displayed in the header of the site)
-a product detail page, showing the product's title, image, credit redemption value, brand and any category associated with the item
-a my account page, with:
*a list of the pluses (coupons/credit added to account) and the minuses (orders placed/credits subtracted from account) to show a detailed description of their history on the site)
*an area for users to edit their name, phone number, address etc
*an area for users to add / edit their casino membership number and casino
*an area for users to add a coupon to their account
-a cart / checkout process:
*cart displaying items and their total
*entering / selecting an address from their account
*review order details page where they can submit their order (and warning the user that doing so will subtract the required credits from their account)

remember that no ecommerce or money is used on the site.. users are spending their credits and checkout their cart with the credits they accumulated, so the items each have a credit redemption value and the checkout process is shown in credits.

we are not very particular with any design preference, other than we'd like it to be predominately white.

If designing the site with css please make sure to use bootstrap in your designs. thanks!

Target Market(s)

adults 45-65

Industry/Entity Type

Casino

Coding

Coded - Design and coding required

Number of Pages Required

5+ page

Font styles to use
Sans Serif

Requirements
Must have
• css must use with bootstrap
Nice to have
• simplified, easy interface. we are targeting an older crowd and dont want to confuse them
Should not have
• the site shouldnt have any dollar values. all product prices, checkout totals and user accrual's (in the my account page) should be in credits

```html
<!DOCTYPE html>
<html lang="en">
<head>
<meta charset="utf-8">
<title>Lark Vista Perks</title>
<link rel="stylesheet" href="https://fonts.googleapis.com/css2?family=Roboto:wght@400;500;700&family=Open+Sans:wght@400;600;700&display=swap">
<style>
:root{
  --blue:#2fa6dc;
  --blue-dark:#1f8fc4;
  --ink:#333;
  --ink-soft:#555;
  --muted:#777;
  --line:#d8d8d8;
  --slate:#5d6368;
  --white:#fff;
  --bg-soft:#f4f4f4;
}
*{box-sizing:border-box;margin:0;padding:0}
html,body{width:1200px;height:2372px;overflow:hidden;background:var(--white)}
body{position:relative;font-family:"Open Sans",Arial,sans-serif;color:var(--ink)}
.abs{position:absolute}
a{color:inherit;text-decoration:none}

/* top bar */
.topbar{left:0;top:0;width:1200px;height:29px;background:var(--blue);color:var(--white);font-size:12px;display:flex;align-items:center;justify-content:space-between;padding:0 98px}
.topbar span{display:inline-flex;align-items:center;gap:6px;margin-right:18px}
.topbar .links span{margin:0 0 0 10px}
.topbar .sep{opacity:.8;margin:0 0 0 10px}
.topbar svg{width:12px;height:12px;fill:var(--white)}

/* header */
.brand{left:98px;top:49px;display:flex;align-items:center;gap:10px}
.brand-mark{width:36px;height:36px;background:var(--blue);border-radius:4px}
.brand-name{font-family:"Roboto",Arial,sans-serif;font-weight:700;font-size:23px;color:#222}
.search{left:656px;top:47px;width:446px;height:43px;border:1px solid #c9c9c9;display:flex;align-items:center;padding-left:24px;gap:14px;font-size:12px;color:#999;letter-spacing:.5px}
.search svg{width:16px;height:16px}

.mainnav{left:0;top:110px;width:1200px;height:40px;border-top:1px solid var(--line);border-bottom:1px solid var(--line)}
.mainnav a{position:absolute;top:9px;transform:translateX(-50%);font-size:16px;color:#333;white-space:nowrap}
.mainnav a.active{color:var(--blue)}

/* hero */
.hero{left:0;top:150px;width:1200px;height:407px;background:radial-gradient(ellipse at 50% 45%,#8a6a2f 0%,#5a4a34 35%,#3e3f42 70%,#55585c 100%)}
.hero-title{left:0;top:236px;width:1200px;text-align:center;font-family:"Roboto",Arial,sans-serif;font-weight:700;font-size:72px;color:var(--white);text-shadow:0 2px 6px rgba(0,0,0,.35)}
.hero-sub{left:0;top:322px;width:1200px;text-align:center;font-size:23px;color:var(--white)}
.hero-btn{left:508px;top:372px;width:184px;height:41px;border:2px solid var(--white);color:var(--white);font-family:"Roboto",Arial,sans-serif;font-weight:700;font-size:16px;display:flex;align-items:center;justify-content:center}
.dots{left:558px;top:492px;display:flex;gap:6px}
.dots i{width:16px;height:16px;border-radius:50%;border:2px solid var(--white)}
.dots i.on{background:var(--blue)}

/* categories */
.categories{left:98px;top:632px;width:260px;height:763px;border:1px solid #cfcfcf}
.categories h3{background:var(--slate);color:var(--white);font-family:"Roboto",Arial,sans-serif;font-weight:700;font-size:19px;height:38px;line-height:38px;padding-left:22px}
.categories ul{list-style:none;padding:20px 0 0 22px}
.categories li{height:41px;font-size:13px;color:#444;display:flex;align-items:center;gap:12px;margin-top:-6px}
.categories li svg{width:13px;height:13px}

/* featured */
.section-title{font-family:"Roboto",Arial,sans-serif;font-weight:700;font-size:23px;color:#333}
.featured-title{left:392px;top:626px}
.filter{left:854px;top:628px;display:flex;align-items:center;gap:10px;font-size:12px;color:#555}
.filter .select{width:117px;height:32px;border:1px solid #c9c9c9;position:relative}
.filter .select::after{content:"";position:absolute;right:0;top:0;width:38px;height:30px;border-left:1px solid #c9c9c9}
.filter .select svg{position:absolute;right:14px;top:12px;width:10px;height:6px;z-index:1}
.viewicons{left:1052px;top:636px;display:flex;gap:10px}
.viewicons svg{width:18px;height:14px}
.featured-rule{left:392px;top:672px;width:710px;height:1px;background:var(--line)}

.product{position:absolute;width:223px}
.product .frame{width:223px;height:176px;background:var(--white);box-shadow:0 0 0 1px #e2e2e2,inset 0 0 18px rgba(0,0,0,.12);display:flex;align-items:center;justify-content:center}
.product .photo{width:140px;height:110px;border-radius:8px}
.product h4{margin-top:26px;font-size:14px;font-weight:700;color:#333}
.product .code{margin-top:10px;font-size:13px;color:#444}
.product .code b{font-weight:700}
.product .actions{margin-top:14px;display:flex;gap:10px}
.btn-primary{width:104px;height:28px;background:var(--blue);color:var(--white);font-size:11px;font-weight:600;display:flex;align-items:center;justify-content:center}
.btn-outline{width:105px;height:28px;border:1px solid #bfbfbf;color:#555;font-size:11px;display:flex;align-items:center;justify-content:center}
.bottom-rule{left:392px;top:1358px;width:710px;height:1px;background:var(--line)}
.viewmore{left:392px;top:1384px;font-size:12px;font-weight:700;color:var(--blue)}

/* earn band */
.earn{left:0;top:1467px;width:1200px;height:209px;background:var(--blue)}
.earn h2{position:absolute;left:0;top:38px;width:1200px;text-align:center;font-family:"Roboto",Arial,sans-serif;font-weight:700;font-size:23px;color:var(--white)}
.partner{position:absolute;top:95px;width:153px;height:66px;background:var(--white);border:1px solid #d7e9f3;display:flex;align-items:center;justify-content:center}
.partner i{width:100px;height:26px;background:#d6d6d6;border-radius:3px}
.round-arrow{position:absolute;width:42px;height:42px;border-radius:50%;border:2px solid var(--white);display:flex;align-items:center;justify-content:center}
.round-arrow svg{width:12px;height:14px}

/* redeem options */
.redeem-title{left:0;top:1732px;width:1200px;text-align:center}
.option{position:absolute;top:1798px;width:168px}
.option .thumb{width:168px;height:118px;border:1px solid #d0d0d0;padding:6px;background:var(--white);box-shadow:0 1px 3px rgba(0,0,0,.12)}
.option .thumb div{width:100%;height:100%}
.option p{margin-top:17px;font-size:12px;line-height:20px;color:#444}
.grey-arrow{position:absolute;top:1840px;width:34px;height:34px;border-radius:50%;border:1px solid #c8c8c8;background:var(--white);display:flex;align-items:center;justify-content:center}
.grey-arrow svg{width:9px;height:12px}

/* footer */
.footer-rule{left:0;top:2028px;width:1200px;height:4px;background:var(--blue)}
.fcol{position:absolute;top:2068px}
.fcol h5{font-family:"Roboto",Arial,sans-serif;font-weight:500;font-size:19px;color:#222;margin-bottom:14px}
.fcol ul{list-style:none}
.fcol li{font-size:12px;color:#555;height:27.5px}
.fdiv{position:absolute;top:2068px;width:1px;height:200px;background:#e3e3e3}
.newsletter p{font-size:12px;color:#555;margin-bottom:14px}
.signup{display:flex}
.signup .input{width:230px;height:36px;border:1px solid #c9c9c9;font-size:12px;color:#777;padding-left:12px;display:flex;align-items:center}
.signup .go{width:94px;height:36px;background:var(--blue);color:var(--white);font-size:13px;font-weight:700;display:flex;align-items:center;justify-content:center}
.newsletter h5.stay{margin:14px 0 10px}
.social{display:flex;gap:7px}
.social i{width:32px;height:32px;border-radius:50%}
.copy-rule{left:98px;top:2296px;width:1004px;height:1px;background:#e3e3e3}
.copyright{left:0;top:2324px;width:1200px;text-align:center;font-size:12px;color:#555}
</style>
</head>
<body>

<div class="abs topbar">
  <div>
    <span><svg viewBox="0 0 24 24"><path d="M6.6 10.8a15 15 0 0 0 6.6 6.6l2.2-2.2c.3-.3.7-.4 1-.2 1.1.4 2.3.6 3.6.6.6 0 1 .4 1 1V20c0 .6-.4 1-1 1A17 17 0 0 1 3 4c0-.6.4-1 1-1h3.5c.6 0 1 .4 1 1 0 1.3.2 2.5.6 3.6.1.3 0 .7-.2 1z"/></svg>1 800 555 0142</span>
    <span><svg viewBox="0 0 24 24"><path d="M2 5h20v14H2zm2 2v.5l8 5 8-5V7l-8 5z"/></svg>hello@larkvistaperks.com</span>
  </div>
  <div class="links">
    <span><svg viewBox="0 0 24 24"><circle cx="8" cy="8" r="4"/><circle cx="17" cy="9" r="3"/><path d="M0 20c0-4 4-6 8-6s8 2 8 6zM15 14c4 0 9 1 9 5h-7c0-2-1-4-2-5z"/></svg>Membership</span><span class="sep">|</span>
    <span><svg viewBox="0 0 24 24"><circle cx="12" cy="7" r="5"/><path d="M2 22c0-6 5-8 10-8s10 2 10 8z"/></svg>My Account</span><span class="sep">|</span>
    <span><svg viewBox="0 0 24 24"><path d="M5 10h14v12H5zM8 10V7a4 4 0 0 1 8 0v3h-2V7a2 2 0 0 0-4 0v3z"/></svg>Sign in</span><span class="sep">|</span>
    <span><svg viewBox="0 0 24 24"><path d="M3 17.5V21h3.5L18 9.5 14.5 6zM20.7 6.8l-3.5-3.5-2 2 3.5 3.5z"/></svg>Create an account</span>
  </div>
</div>

<div class="abs brand"><i class="brand-mark"></i><span class="brand-name">LARK VISTA PERKS</span></div>
<div class="abs search"><svg viewBox="0 0 24 24" fill="none" stroke="#888" stroke-width="2.5"><circle cx="10" cy="10" r="7"/><path d="M15 15l7 7"/></svg>SEARCH</div>

<nav class="abs mainnav">
  <a class="active" style="left:170px">Home</a>
  <a style="left:305px">About Us</a>
  <a style="left:463px">Earn Points</a>
  <a style="left:648px">Redeem Points</a>
  <a style="left:835px">Multiply Points</a>
  <a style="left:1010px">Contact Us</a>
</nav>

<div class="abs hero" role="img" aria-label="Photo of hands holding a tablet showing a discount coupon"></div>
<div class="abs hero-title">LARK VISTA PERKS</div>
<div class="abs hero-sub">We are a coupon redemption company</div>
<div class="abs hero-btn">REDEEM NOW!</div>
<div class="abs dots"><i class="on"></i><i></i><i></i><i></i></div>

<aside class="abs categories">
  <h3>CATEGORIES</h3>
  <ul>
    <li><svg viewBox="0 0 14 14"><circle cx="7" cy="7" r="7" fill="#2fa6dc"/><path d="M3.5 7.2l2.3 2.2 4.6-4.6" fill="none" stroke="#fff" stroke-width="1.8"/></svg>New Products</li>
    <li><svg viewBox="0 0 14 14"><circle cx="7" cy="7" r="7" fill="#2fa6dc"/><path d="M3.5 7.2l2.3 2.2 4.6-4.6" fill="none" stroke="#fff" stroke-width="1.8"/></svg>Specials</li>
    <li><svg viewBox="0 0 14 14"><circle cx="7" cy="7" r="7" fill="#2fa6dc"/><path d="M3.5 7.2l2.3 2.2 4.6-4.6" fill="none" stroke="#fff" stroke-width="1.8"/></svg>Featured</li>
    <li><svg viewBox="0 0 14 14"><circle cx="7" cy="7" r="7" fill="#2fa6dc"/><path d="M3.5 7.2l2.3 2.2 4.6-4.6" fill="none" stroke="#fff" stroke-width="1.8"/></svg>Bestsellers</li>
    <li><svg viewBox="0 0 14 14"><circle cx="7" cy="7" r="7" fill="#2fa6dc"/><path d="M3.5 7.2l2.3 2.2 4.6-4.6" fill="none" stroke="#fff" stroke-width="1.8"/></svg>Books &amp; Magazines</li>
    <li><svg viewBox="0 0 14 14"><circle cx="7" cy="7" r="7" fill="#2fa6dc"/><path d="M3.5 7.2l2.3 2.2 4.6-4.6" fill="none" stroke="#fff" stroke-width="1.8"/></svg>Movies, Music &amp; Games</li>
    <li><svg viewBox="0 0 14 14"><circle cx="7" cy="7" r="7" fill="#2fa6dc"/><path d="M3.5 7.2l2.3 2.2 4.6-4.6" fill="none" stroke="#fff" stroke-width="1.8"/></svg>Digital Downloads</li>
    <li><svg viewBox="0 0 14 14"><circle cx="7" cy="7" r="7" fill="#2fa6dc"/><path d="M3.5 7.2l2.3 2.2 4.6-4.6" fill="none" stroke="#fff" stroke-width="1.8"/></svg>Computers &amp; Office</li>
    <li><svg viewBox="0 0 14 14"><circle cx="7" cy="7" r="7" fill="#2fa6dc"/><path d="M3.5 7.2l2.3 2.2 4.6-4.6" fill="none" stroke="#fff" stroke-width="1.8"/></svg>Electronics</li>
    <li><svg viewBox="0 0 14 14"><circle cx="7" cy="7" r="7" fill="#2fa6dc"/><path d="M3.5 7.2l2.3 2.2 4.6-4.6" fill="none" stroke="#fff" stroke-width="1.8"/></svg>Sports &amp; Outdoors</li>
    <li><svg viewBox="0 0 14 14"><circle cx="7" cy="7" r="7" fill="#2fa6dc"/><path d="M3.5 7.2l2.3 2.2 4.6-4.6" fill="none" stroke="#fff" stroke-width="1.8"/></svg>Specials</li>
    <li><svg viewBox="0 0 14 14"><circle cx="7" cy="7" r="7" fill="#2fa6dc"/><path d="M3.5 7.2l2.3 2.2 4.6-4.6" fill="none" stroke="#fff" stroke-width="1.8"/></svg>Featured</li>
    <li><svg viewBox="0 0 14 14"><circle cx="7" cy="7" r="7" fill="#2fa6dc"/><path d="M3.5 7.2l2.3 2.2 4.6-4.6" fill="none" stroke="#fff" stroke-width="1.8"/></svg>Bestsellers</li>
    <li><svg viewBox="0 0 14 14"><circle cx="7" cy="7" r="7" fill="#2fa6dc"/><path d="M3.5 7.2l2.3 2.2 4.6-4.6" fill="none" stroke="#fff" stroke-width="1.8"/></svg>Books &amp; Magazines</li>
    <li><svg viewBox="0 0 14 14"><circle cx="7" cy="7" r="7" fill="#2fa6dc"/><path d="M3.5 7.2l2.3 2.2 4.6-4.6" fill="none" stroke="#fff" stroke-width="1.8"/></svg>Movies, Music &amp; Games</li>
    <li><svg viewBox="0 0 14 14"><circle cx="7" cy="7" r="7" fill="#2fa6dc"/><path d="M3.5 7.2l2.3 2.2 4.6-4.6" fill="none" stroke="#fff" stroke-width="1.8"/></svg>Digital Downloads</li>
  </ul>
</aside>

<h2 class="abs section-title featured-title">FEATURED PRODUCTS</h2>
<div class="abs filter">Filter By <div class="select"><svg viewBox="0 0 10 6"><path d="M0 0h10L5 6z" fill="#777"/></svg></div></div>
<div class="abs viewicons">
  <svg viewBox="0 0 18 14" fill="#888"><rect x="0" y="0" width="4" height="3"/><rect x="7" y="0" width="4" height="3"/><rect x="14" y="0" width="4" height="3"/><rect x="0" y="5.5" width="4" height="3"/><rect x="7" y="5.5" width="4" height="3"/><rect x="14" y="5.5" width="4" height="3"/><rect x="0" y="11" width="4" height="3"/><rect x="7" y="11" width="4" height="3"/><rect x="14" y="11" width="4" height="3"/></svg>
  <svg viewBox="0 0 18 14" fill="#888"><rect x="0" y="0" width="4" height="3"/><rect x="6" y="0" width="12" height="3"/><rect x="0" y="5.5" width="4" height="3"/><rect x="6" y="5.5" width="12" height="3"/><rect x="0" y="11" width="4" height="3"/><rect x="6" y="11" width="12" height="3"/></svg>
</div>
<div class="abs featured-rule"></div>

<div class="product" style="left:392px;top:711px"><div class="frame"><div class="photo" role="img" aria-label="Smartphone with shopping bags and cards" style="background:linear-gradient(135deg,#4a4d57,#c94b5a 60%,#e6b34a)"></div></div><h4>At vero eos et accusam et..</h4><div class="code">Item Code : <b>DET387</b></div><div class="actions"><a class="btn-primary">REDEEM NOW</a><a class="btn-outline">MORE DETAILS</a></div></div>
<div class="product" style="left:634px;top:711px"><div class="frame"><div class="photo" role="img" aria-label="Pair of wristwatches" style="background:linear-gradient(135deg,#3a3a3a,#d9d6cf 50%,#8c6a3e)"></div></div><h4>At vero eos et accusam et..</h4><div class="code">Item Code : <b>DET387</b></div><div class="actions"><a class="btn-primary">REDEEM NOW</a><a class="btn-outline">MORE DETAILS</a></div></div>
<div class="product" style="left:877px;top:711px"><div class="frame"><div class="photo" role="img" aria-label="Red leather handbag" style="background:radial-gradient(ellipse at 50% 60%,#e0202c,#b5121c 70%,#fff 71%)"></div></div><h4>At vero eos et accusam et..</h4><div class="code">Item Code : <b>DET387</b></div><div class="actions"><a class="btn-primary">REDEEM NOW</a><a class="btn-outline">MORE DETAILS</a></div></div>

<div class="product" style="left:392px;top:1039px"><div class="frame"><div class="photo" role="img" aria-label="Aviator sunglasses" style="background:radial-gradient(ellipse at 50% 55%,#4d504f,#7a7d7c 55%,#fff 72%)"></div></div><h4>At vero eos et accusam et..</h4><div class="code">Item Code : <b>DET387</b></div><div class="actions"><a class="btn-primary">REDEEM NOW</a><a class="btn-outline">MORE DETAILS</a></div></div>
<div class="product" style="left:634px;top:1039px"><div class="frame"><div class="photo" role="img" aria-label="Black tablet computer" style="background:radial-gradient(ellipse at 50% 50%,#1a1a1a,#333 60%,#fff 72%)"></div></div><h4>At vero eos et accusam et..</h4><div class="code">Item Code : <b>DET387</b></div><div class="actions"><a class="btn-primary">REDEEM NOW</a><a class="btn-outline">MORE DETAILS</a></div></div>
<div class="product" style="left:877px;top:1039px"><div class="frame"><div class="photo" role="img" aria-label="Blue clasp coin purse" style="background:radial-gradient(ellipse at 50% 60%,#1f5fd4,#0d3fa6 68%,#fff 70%)"></div></div><h4>At vero eos et accusam et..</h4><div class="code">Item Code : <b>DET387</b></div><div class="actions"><a class="btn-primary">REDEEM NOW</a><a class="btn-outline">MORE DETAILS</a></div></div>

<div class="abs bottom-rule"></div>
<a class="abs viewmore">VIEW MORE PRODUCTS &gt;&gt;</a>

<section class="abs earn">
  <h2>EARN POINTS ON ONLINE SHOPPING AT</h2>
  <div class="round-arrow" style="left:64px;top:104px"><svg viewBox="0 0 12 14"><path d="M9 1L3 7l6 6" fill="none" stroke="#fff" stroke-width="2"/></svg></div>
  <div class="partner" style="left:150px"><i></i></div>
  <div class="partner" style="left:336px"><i></i></div>
  <div class="partner" style="left:523px"><i></i></div>
  <div class="partner" style="left:711px"><i></i></div>
  <div class="partner" style="left:896px"><i></i></div>
  <div class="round-arrow" style="left:1096px;top:104px"><svg viewBox="0 0 12 14"><path d="M3 1l6 6-6 6" fill="none" stroke="#fff" stroke-width="2"/></svg></div>
</section>

<h2 class="abs section-title redeem-title">REDEEM POINTS FROM MULTIPLE REWARDS OPTIONS</h2>
<div class="grey-arrow" style="left:58px"><svg viewBox="0 0 9 12"><path d="M7 1L2 6l5 5" fill="none" stroke="#888" stroke-width="1.6"/></svg></div>
<div class="option" style="left:98px"><div class="thumb"><div role="img" aria-label="Tablet showing a discount coupon" style="background:linear-gradient(135deg,#3d8fc4,#e8b23a 55%,#d96b2a)"></div></div><p>At vero eos et accusamus et<br>iusto odio dignissimos</p></div>
<div class="option" style="left:307px"><div class="thumb"><div role="img" aria-label="Stack of clipped paper coupons" style="background:linear-gradient(135deg,#d8d8d8,#a9b4bf 50%,#e4e0d8)"></div></div><p>At vero eos et accusamus et<br>iusto odio dignissimos</p></div>
<div class="option" style="left:517px"><div class="thumb"><div role="img" aria-label="Hand holding a green discount gift card" style="background:linear-gradient(135deg,#f2f2f2,#7cc242 45%,#e9dccf)"></div></div><p>At vero eos et accusamus et<br>iusto odio dignissimos</p></div>
<div class="option" style="left:726px"><div class="thumb"><div role="img" aria-label="Hands using a phone and a payment card" style="background:linear-gradient(135deg,#b98a5c,#5a4030 55%,#2a2a2a)"></div></div><p>At vero eos et accusamus et<br>iusto odio dignissimos</p></div>
<div class="option" style="left:935px"><div class="thumb"><div role="img" aria-label="Gift vouchers tied with pink ribbon" style="background:linear-gradient(135deg,#f1e4d6,#e8c9c0 50%,#d94a6a)"></div></div><p>At vero eos et accusamus et<br>iusto odio dignissimos</p></div>
<div class="grey-arrow" style="left:1105px"><svg viewBox="0 0 9 12"><path d="M2 1l5 5-5 5" fill="none" stroke="#888" stroke-width="1.6"/></svg></div>

<div class="abs footer-rule"></div>

<div class="fcol" style="left:100px"><h5>Information</h5><ul><li>Gift Registry</li><li>Gift Certificates</li><li>Privacy Policy</li><li>About Us</li><li>Contact Us</li><li>Site Map</li></ul></div>
<div class="fdiv" style="left:259px"></div>
<div class="fcol" style="left:304px"><h5>Help &amp; support</h5><ul><li>Recommended Reading</li><li>Submit your Story</li><li>Contact Us</li><li>Frequently Asked Questions</li><li>How to Order</li></ul></div>
<div class="fdiv" style="left:507px"></div>
<div class="fcol" style="left:552px"><h5>My Account</h5><ul><li>Delivery Information</li><li>My Account</li><li>Order Tracking</li><li>Reminder Service</li><li>Shipping, Returns &amp; Fees</li></ul></div>
<div class="fdiv" style="left:732px"></div>
<div class="fcol newsletter" style="left:778px">
  <h5>Newsletter Signup</h5>
  <p>Register your email address to get information about us</p>
  <div class="signup"><div class="input">Email Address</div><div class="go">SIGN UP</div></div>
  <h5 class="stay">Stay Connected</h5>
  <div class="social"><i style="background:#4cb58c"></i><i style="background:#3b5c9a"></i><i style="background:#4ab0e3"></i><i style="background:#d9473a"></i><i style="background:#4f6e8f"></i><i style="background:#3fb2d6"></i><i style="background:#c4202a"></i><i style="background:#c8232c"></i></div>
</div>

<div class="abs copy-rule"></div>
<div class="abs copyright">Copyrights © 2017, Lark Vista Perks. All Rights Reserved &nbsp;|&nbsp; Privacy Policy | Terms of Use | Feedback</div>

</body>
</html>
```